Brookmere Osteopathy flyer

I want a clean clear DL flyer (but also want an A4 poster) promoting a new Osteopathic business in a semi rural area in Tasmania (Australia).
It can have pictures like the examples attached to show people what Osteopathy is (its like Chiropractic and physiotherapy).
I am the sole practioner and am male, so any pictures would be best to be a white male if possible.
I've attached some wording, you can use all, or none of it
I don't have a phone number for the business yet
info@brookmereosteopathy.example
www.brookmereosteopathy.example
Target Market(s)
Australians, from tradies, professionals, babies to retired people
Industry/Entity Type
Health
Look and feel

```html
<!DOCTYPE html>
<html lang="en">
<head>
<meta charset="utf-8">
<title>Brookmere Osteopathy – Flyer</title>
<link rel="stylesheet" href="https://fonts.googleapis.com/css2?family=Poppins:ital,wght@0,500;0,600;0,700;0,800;1,400;1,600&family=Nunito+Sans:wght@500&family=Lora:ital,wght@1,500&display=swap">
<style>
  :root {
    --backdrop: #4f4f4f;
    --paper: #ffffff;
    --blue: #1190d3;
    --blue-deep: #0a6fae;
    --blue-soft: #3aa9e0;
    --navy: #103f6b;
    --orange: #f6913a;
    --ink: #2c2c2c;
    --ink-soft: #444444;
    --photo-skin: #d9a57c;
    --photo-cool: #8fa7b2;
  }
  * { box-sizing: border-box; margin: 0; padding: 0; }
  html, body { width: 678px; height: 1200px; overflow: hidden; background: var(--backdrop); }
  .flyer {
    position: absolute; left: 82px; top: 56px; width: 513px; height: 1090px;
    background: var(--paper); overflow: hidden;
    font-family: "Nunito Sans", sans-serif; color: var(--ink);
  }
  .flyer__header { position: absolute; left: 0; top: 0; width: 513px; height: 220px; }
  .brand-badge {
    position: absolute; left: 179px; top: 37px; width: 156px; height: 156px;
    border-radius: 50%; background: var(--paper);
    box-shadow: 0 4px 10px rgba(0,0,0,.18);
    display: flex; align-items: center; justify-content: center; text-align: center;
  }
  .brand-badge__name {
    font-family: "Poppins", sans-serif; font-weight: 600; font-size: 17px;
    line-height: 1.2; color: var(--blue);
  }
  .headline { position: absolute; left: 0; width: 100%; text-align: center; }
  .headline__main {
    top: 196px; left: 6px; font-family: "Poppins", sans-serif; font-weight: 800;
    font-size: 61px; line-height: 1; color: var(--blue); letter-spacing: -0.5px;
  }
  .headline__accent {
    top: 258px; left: 26px; font-family: "Lora", serif; font-style: italic; font-weight: 500;
    font-size: 56px; line-height: 1; color: var(--orange);
  }
  .reasons__title {
    position: absolute; left: 36px; top: 339px; width: 443px; height: 76px;
    border-radius: 24px 24px 0 0;
    background: linear-gradient(100deg, var(--blue) 0%, var(--blue) 55%, var(--blue-deep) 100%);
    color: #fff; font-family: "Poppins", sans-serif; font-weight: 600;
    font-size: 23px; line-height: 29px; text-align: center; padding-top: 9px;
  }
  .reasons__list {
    position: absolute; top: 429px; list-style: none;
    font-size: 18.5px; line-height: 23px; color: var(--ink-soft);
  }
  .reasons__list--left { left: 45px; }
  .reasons__list--right { left: 276px; }
  .reasons__item { position: relative; padding-left: 22px; }
  .reasons__icon { position: absolute; left: 0; top: 4px; width: 15px; height: 16px; }
  .photo { position: absolute; }
  .photo--wide { left: 36px; top: 594px; width: 444px; height: 145px; border-radius: 22px;
    background: linear-gradient(90deg, var(--photo-cool) 0%, var(--photo-skin) 35%, var(--photo-skin) 75%, #5a4031 100%); }
  .photo--left { left: 36px; top: 745px; width: 218px; height: 119px; border-radius: 20px;
    background: linear-gradient(120deg, #2c3450 0%, var(--photo-skin) 45%, #e7c4a6 100%); }
  .photo--right { left: 262px; top: 745px; width: 218px; height: 119px; border-radius: 20px;
    background: linear-gradient(120deg, #cfa07e 0%, var(--photo-skin) 55%, #f1ece6 100%); }
  .about {
    position: absolute; left: 0; top: 889px; width: 513px; height: 107px;
    background: var(--navy); color: #fff; text-align: center;
    font-family: "Poppins", sans-serif; font-style: italic; font-weight: 400;
    font-size: 13.2px; line-height: 18.5px; padding: 16px 26px 0;
  }
  .about em { color: var(--orange); font-weight: 600; }
  .cta {
    position: absolute; left: 104px; top: 978px; width: 306px; height: 35px;
    border-radius: 18px; background: var(--orange); color: #fff;
    font-family: "Poppins", sans-serif; font-weight: 600; font-size: 21px;
    line-height: 35px; text-align: center; letter-spacing: -0.3px;
  }
  .contact { position: absolute; left: 0; width: 100%; text-align: center;
    font-family: "Poppins", sans-serif; color: var(--ink); }
  .contact__address { top: 1022px; font-weight: 500; font-size: 18.5px; letter-spacing: -0.3px; }
  .contact__online { top: 1049px; font-weight: 500; font-size: 12.6px; letter-spacing: -0.2px; }
  .contact__icon { display: inline-block; vertical-align: -2px; margin-right: 3px; }
  .contact__gap { display: inline-block; width: 14px; }
</style>
</head>
<body>
<main class="flyer">
  <svg class="flyer__header" viewBox="0 0 513 220" aria-hidden="true">
    <defs>
      <linearGradient id="bandGrad" x1="0" y1="0" x2="1" y2="0">
        <stop offset="0" stop-color="#0b6fad"/>
        <stop offset="1" stop-color="#1396d7"/>
      </linearGradient>
    </defs>
    <path d="M0 0 H513 V86 Q300 170 256 146 Q120 140 0 87 Z" fill="#0e87c9"/>
    <path d="M0 82 Q130 150 256 150 Q390 148 513 78 V86 Q390 170 256 150 Q120 160 0 87 Z" fill="#3aa9e0"/>
    <path d="M0 0 H513 V70 Q380 130 256 130 Q120 130 0 72 Z" fill="url(#bandGrad)"/>
    <path d="M0 72 Q120 140 256 146 Q110 142 0 78 Z" fill="#3aa9e0"/>
    <path d="M0 77 Q110 150 256 150 Q400 150 513 78 L513 84 Q400 165 256 165 Q110 165 0 81 Z" fill="var(--orange)"/>
  </svg>

  <div class="brand-badge">
    <span class="brand-badge__name">Brookmere<br>Osteopathy</span>
  </div>

  <h1 class="headline headline__main">Osteopathy</h1>
  <p class="headline headline__accent">that Cares</p>

  <h2 class="reasons__title">Common reasons people<br>visit an osteopath</h2>

  <ul class="reasons__list reasons__list--left">
    <li class="reasons__item"><svg class="reasons__icon" viewBox="0 0 15 16"><path d="M7.5 1 L13.5 4.5 V11.5 L7.5 15 L1.5 11.5 V4.5 Z" fill="none" stroke="#f6913a" stroke-width="1.4"/><path d="M4.6 8 L6.8 10.2 L10.6 5.9" fill="none" stroke="#f6913a" stroke-width="1.5"/></svg>Back / neck pain</li>
    <li class="reasons__item"><svg class="reasons__icon" viewBox="0 0 15 16"><path d="M7.5 1 L13.5 4.5 V11.5 L7.5 15 L1.5 11.5 V4.5 Z" fill="none" stroke="#f6913a" stroke-width="1.4"/><path d="M4.6 8 L6.8 10.2 L10.6 5.9" fill="none" stroke="#f6913a" stroke-width="1.5"/></svg>Headaches / migraines</li>
    <li class="reasons__item"><svg class="reasons__icon" viewBox="0 0 15 16"><path d="M7.5 1 L13.5 4.5 V11.5 L7.5 15 L1.5 11.5 V4.5 Z" fill="none" stroke="#f6913a" stroke-width="1.4"/><path d="M4.6 8 L6.8 10.2 L10.6 5.9" fill="none" stroke="#f6913a" stroke-width="1.5"/></svg>Joint and muscle pain</li>
    <li class="reasons__item"><svg class="reasons__icon" viewBox="0 0 15 16"><path d="M7.5 1 L13.5 4.5 V11.5 L7.5 15 L1.5 11.5 V4.5 Z" fill="none" stroke="#f6913a" stroke-width="1.4"/><path d="M4.6 8 L6.8 10.2 L10.6 5.9" fill="none" stroke="#f6913a" stroke-width="1.5"/></svg>Pregnancy-related<br>discomfort</li>
    <li class="reasons__item"><svg class="reasons__icon" viewBox="0 0 15 16"><path d="M7.5 1 L13.5 4.5 V11.5 L7.5 15 L1.5 11.5 V4.5 Z" fill="none" stroke="#f6913a" stroke-width="1.4"/><path d="M4.6 8 L6.8 10.2 L10.6 5.9" fill="none" stroke="#f6913a" stroke-width="1.5"/></svg>Disc related issues</li>
  </ul>
  <ul class="reasons__list reasons__list--right">
    <li class="reasons__item"><svg class="reasons__icon" viewBox="0 0 15 16"><path d="M7.5 1 L13.5 4.5 V11.5 L7.5 15 L1.5 11.5 V4.5 Z" fill="none" stroke="#f6913a" stroke-width="1.4"/><path d="M4.6 8 L6.8 10.2 L10.6 5.9" fill="none" stroke="#f6913a" stroke-width="1.5"/></svg>Sciatica</li>
    <li class="reasons__item"><svg class="reasons__icon" viewBox="0 0 15 16"><path d="M7.5 1 L13.5 4.5 V11.5 L7.5 15 L1.5 11.5 V4.5 Z" fill="none" stroke="#f6913a" stroke-width="1.4"/><path d="M4.6 8 L6.8 10.2 L10.6 5.9" fill="none" stroke="#f6913a" stroke-width="1.5"/></svg>Plantar fasciitis</li>
    <li class="reasons__item"><svg class="reasons__icon" viewBox="0 0 15 16"><path d="M7.5 1 L13.5 4.5 V11.5 L7.5 15 L1.5 11.5 V4.5 Z" fill="none" stroke="#f6913a" stroke-width="1.4"/><path d="M4.6 8 L6.8 10.2 L10.6 5.9" fill="none" stroke="#f6913a" stroke-width="1.5"/></svg>Tendonitis / Bursitis</li>
    <li class="reasons__item"><svg class="reasons__icon" viewBox="0 0 15 16"><path d="M7.5 1 L13.5 4.5 V11.5 L7.5 15 L1.5 11.5 V4.5 Z" fill="none" stroke="#f6913a" stroke-width="1.4"/><path d="M4.6 8 L6.8 10.2 L10.6 5.9" fill="none" stroke="#f6913a" stroke-width="1.5"/></svg>Adhesive capsulitis<br>(frozen shoulder)</li>
    <li class="reasons__item"><svg class="reasons__icon" viewBox="0 0 15 16"><path d="M7.5 1 L13.5 4.5 V11.5 L7.5 15 L1.5 11.5 V4.5 Z" fill="none" stroke="#f6913a" stroke-width="1.4"/><path d="M4.6 8 L6.8 10.2 L10.6 5.9" fill="none" stroke="#f6913a" stroke-width="1.5"/></svg>Tennis / Golfers elbow</li>
  </ul>

  <div class="photo photo--wide" role="img" aria-label="Photo: osteopath's hands treating the lower back of a patient lying face down"></div>
  <div class="photo photo--left" role="img" aria-label="Photo: practitioner applying hands-on treatment to a patient's back and arm"></div>
  <div class="photo photo--right" role="img" aria-label="Photo: osteopath mobilising a male patient's shoulder blade"></div>

  <p class="about">Osteopaths use a combination of <em>joint manipulation</em>, <em>targeted deep tissue massage</em> and <em>stretching</em> to improve <em>function, relieve pain</em> and support the body’s ability to <em>heal itself.</em></p>

  <p class="cta">Call us Today! 123-456-780</p>

  <p class="contact contact__address"><svg class="contact__icon" width="13" height="17" viewBox="0 0 13 17" aria-hidden="true"><path d="M6.5 1 C3.3 1 1 3.3 1 6.3 C1 10 6.5 16 6.5 16 C6.5 16 12 10 12 6.3 C12 3.3 9.7 1 6.5 1 Z" fill="none" stroke="#f6913a" stroke-width="1.8"/><circle cx="6.5" cy="6.3" r="2" fill="#f6913a"/></svg>42 Ferndale Road, Brookmere</p>
  <p class="contact contact__online"><svg class="contact__icon" width="14" height="14" viewBox="0 0 14 14" aria-hidden="true"><g fill="none" stroke="#f6913a" stroke-width="1"><circle cx="7" cy="7" r="6"/><ellipse cx="7" cy="7" rx="2.6" ry="6"/><path d="M1 7 H13 M2 3.8 H12 M2 10.2 H12"/></g></svg>www.brookmereosteopathy.example<span class="contact__gap"></span><svg class="contact__icon" width="15" height="11" viewBox="0 0 15 11" aria-hidden="true"><g fill="none" stroke="#f6913a" stroke-width="1"><rect x="0.5" y="0.5" width="14" height="10"/><path d="M0.5 0.5 L7.5 6 L14.5 0.5 M0.5 10.5 L5.5 5 M14.5 10.5 L9.5 5"/></g></svg>info@brookmereosteopathy.example</p>
</main>
</body>
</html>
```